Business Card Design Project

We are a construction company in Orange County, CA. We need a two sided business card. We would like the back to be our logo with web URL. Front should included Name, title, address, phone, fax and email address.

our address is
627 West Dorrance Blvd, Suite 308
Anaheim, CA 92718

Our logo files are attached.

Construction

```html
<!DOCTYPE html>
<html lang="en">
<head>
<meta charset="utf-8">
<title>Strata Business Card</title>
<link href="https://fonts.googleapis.com/css2?family=Source+Sans+3:wght@400;700&display=swap" rel="stylesheet">
<style>
  :root {
    --brand-blue: #174a7c;
    --paper: #ffffff;
    --ink: #2b2b2b;
    --backdrop: #e8e5e0;
    --curl-dark: #1a1a1a;
    --curl-mid: #3a3a3a;
    --curl-light: #8a8a8a;
  }
  html, body {
    margin: 0;
    width: 1200px;
    height: 421px;
    overflow: hidden;
    background: var(--backdrop);
    font-family: "Source Sans 3", "Myriad Pro", Arial, sans-serif;
  }
  .canvas { position: relative; width: 1200px; height: 421px; }
  .card {
    position: absolute;
    width: 525px;
    height: 300px;
    box-shadow: 0 1px 3px rgba(0,0,0,.25);
    overflow: hidden;
  }
  .card-front { left: 64px; top: 57px; background: var(--paper); }
  .card-back  { left: 621px; top: 56px; background: var(--brand-blue); }

  .corner-peel { position: absolute; left: 0; top: 0; }

  .person {
    position: absolute;
    right: 20px;
    top: 18px;
    text-align: right;
    color: var(--paper);
  }
  .person-name { font-weight: 700; font-size: 19px; line-height: 22px; }
  .person-title { font-size: 16px; line-height: 22px; }

  .wordmark {
    position: absolute;
    font-weight: 700;
    letter-spacing: -1px;
    line-height: 1;
  }
  .card-front .wordmark { left: 22px; top: 62px; font-size: 84px; color: var(--brand-blue); }
  .card-back .wordmark  { left: 0; right: 0; top: 96px; text-align: center; font-size: 84px; color: var(--paper); }

  .contact-list {
    position: absolute;
    left: 24px;
    top: 173px;
    margin: 0;
    padding: 0;
    list-style: none;
    font-size: 13.5px;
    color: var(--ink);
  }
  .contact-list li { display: flex; align-items: center; height: 16.5px; }
  .contact-list svg { width: 11px; height: 11px; margin-right: 6px; fill: var(--ink); }

  .address {
    position: absolute;
    left: 24px;
    top: 253px;
    margin: 0;
    font-style: normal;
    font-size: 13.5px;
    line-height: 17px;
    color: var(--ink);
  }

  .web-address {
    position: absolute;
    left: 0; right: 0;
    top: 206px;
    text-align: center;
    font-size: 14px;
    letter-spacing: 2px;
    color: var(--paper);
  }
</style>
</head>
<body>
<main class="canvas">
  <section class="card card-front">
    <svg class="corner-peel" width="525" height="300" viewBox="0 0 525 300" aria-hidden="true">
      <defs>
        <linearGradient id="flap-shade" x1="0" y1="0" x2="1" y2="0.55">
          <stop offset="0" stop-color="var(--curl-mid)"/>
          <stop offset="0.55" stop-color="var(--curl-dark)"/>
          <stop offset="0.85" stop-color="var(--curl-mid)"/>
          <stop offset="1" stop-color="var(--curl-light)"/>
        </linearGradient>
        <linearGradient id="roll-shade" x1="0" y1="0" x2="1" y2="0">
          <stop offset="0" stop-color="var(--curl-dark)"/>
          <stop offset="0.5" stop-color="#555555"/>
          <stop offset="1" stop-color="var(--curl-light)"/>
        </linearGradient>
      </defs>
      <path class="peel-reveal" d="M241 0 H525 V113 Z" fill="var(--brand-blue)"/>
      <path class="peel-flap" d="M241 0 L525 113 C500 122 486 140 480 160 C476 172 476 182 481 190 C420 130 320 60 241 0 Z" fill="url(#flap-shade)"/>
      <path class="peel-roll" d="M525 113 L525 128 C505 134 492 148 487 164 C484 174 483 182 481 190 C474 178 474 165 479 152 C487 132 503 119 525 113 Z" fill="url(#roll-shade)"/>
    </svg>

    <div class="person">
      <div class="person-name">Your Name</div>
      <div class="person-title">Title</div>
    </div>

    <div class="wordmark">STRATA</div>

    <ul class="contact-list">
      <li><svg viewBox="0 0 12 12"><path d="M3 1l2 2.5-1.2 1.3a7 7 0 0 0 3.4 3.4L8.5 7 11 9l-1.5 2C5 11 1 7 1 2.5Z"/></svg>01-234-5678</li>
      <li><svg viewBox="0 0 12 12"><path d="M3 1h5v3H3zM1 5h10v5H9v-2H3v2H1z"/></svg>01-234-5678</li>
      <li><svg viewBox="0 0 12 12"><path d="M1 3h10v6H1zM1.5 3.5l4.5 3 4.5-3"/></svg>info@stratabuild.com</li>
      <li><svg viewBox="0 0 12 12"><circle cx="6" cy="6" r="5"/></svg>www.stratabuild.com</li>
    </ul>

    <address class="address">627 West Dorrance Blvd<br>Suite 308, Anaheim, CA&nbsp; 92718</address>
  </section>

  <section class="card card-back">
    <div class="wordmark">STRATA</div>
    <div class="web-address">www.stratabuild.com</div>
  </section>
</main>
</body>
</html>
```